Marketing - Outdoor Vinyl banner, Outdoor Poster, Flyer modifications

Hi, I worked with you in the past and attached flyer designs. It just needs to be tweaked for various prints.
1)Outdoor vinyl banner (4 feet height and 8 feet width) print: Just grand opening pic, logo with name, tagline and call/text us portion.
2)Outdoor Poster (5 feet height and 3 feet width) print: same as above
3) Indoor poster for both horizontal & Vertical prints: Just logo w/ name, tagline, "We are MOVING Next door"
4)Flyer: will give minor modifications to attached flyer designs

```html
<!DOCTYPE html>
<html lang="en">
<head>
<meta charset="utf-8">
<title>Grand Opening Banner</title>
<link rel="stylesheet" href="https://fonts.googleapis.com/css2?family=Oswald:wght@700&family=Montserrat:wght@700;800&family=Hind:wght@600&display=swap">
<style>
  :root {
    --page: #e6e6e6;
    --banner: #f7f8f9;
    --cyan: #1ab4d8;
    --slate: #5f7b9c;
    --navy: #1f3450;
    --muted: #4f6b8c;
    --white: #ffffff;
    --balloon-red: #d0394f;
    --balloon-teal: #27c0d0;
    --balloon-gold: #f2ad1c;
  }
  * { margin: 0; padding: 0; box-sizing: border-box; }
  html, body { width: 1200px; height: 900px; overflow: hidden; background: var(--page); }
  .banner {
    position: absolute; left: 20px; top: 160px;
    width: 1160px; height: 580px;
    background: var(--banner);
    overflow: hidden;
  }
  .photo {
    position: absolute; left: 427px; top: 159px; width: 733px; height: 400px;
    background: linear-gradient(120deg, #e9f2f6 0%, #c7d9e6 35%, #8fb2d4 60%, #c99a86 80%, #e7b8c4 100%);
  }
  .balloons-left {
    position: absolute; left: 0; top: 115px; width: 40px; height: 240px;
    background: linear-gradient(180deg, var(--balloon-red) 0%, var(--balloon-red) 35%, var(--balloon-gold) 55%, var(--balloon-gold) 75%, var(--balloon-teal) 100%);
    border-radius: 0 40px 40px 0;
    opacity: .9;
  }
  .balloons-right {
    position: absolute; right: 0; top: 0; width: 110px; height: 330px;
    background: linear-gradient(180deg, var(--balloon-red) 0%, var(--balloon-teal) 30%, var(--balloon-red) 55%, var(--balloon-gold) 75%, var(--balloon-teal) 100%);
    border-radius: 60px 0 0 60px;
    opacity: .9;
  }
  .wave { position: absolute; left: 0; top: 0; width: 1160px; height: 580px; }
  .headline-box {
    position: absolute; left: 40px; top: 44px; width: 608px; height: 110px;
    border: 5px solid var(--cyan); border-radius: 12px;
    background: var(--white); padding: 5px;
  }
  .headline {
    width: 100%; height: 100%;
    background: var(--slate); border-radius: 6px;
    display: flex; align-items: center; justify-content: center;
    font-family: "Oswald", sans-serif; font-weight: 700;
    font-size: 76px; letter-spacing: 1px; color: var(--white);
  }
  .brand {
    position: absolute; left: 712px; top: 62px;
    display: flex; align-items: center; gap: 14px;
  }
  .brand-mark { width: 46px; height: 46px; border-radius: 50%; background: var(--cyan); }
  .brand-name {
    font-family: "Montserrat", sans-serif; font-weight: 700;
    font-size: 36px; color: var(--cyan); letter-spacing: 1px;
  }
  .cta {
    position: absolute; left: 42px; top: 190px;
    font-family: "Montserrat", sans-serif; font-weight: 800;
    font-size: 37px; color: var(--navy);
  }
  .phone {
    position: absolute; left: 40px; top: 251px; width: 426px; height: 57px;
    display: flex; border-radius: 10px; overflow: hidden;
  }
  .phone-icon {
    width: 81px; background: var(--navy);
    display: flex; align-items: center; justify-content: center;
  }
  .phone-number {
    flex: 1; background: var(--cyan);
    display: flex; align-items: center; padding-left: 20px;
    font-family: "Montserrat", sans-serif; font-weight: 700;
    font-size: 42px; color: var(--white); letter-spacing: 1px;
  }
  .hours {
    position: absolute; left: 50px; top: 330px;
    font-family: "Hind", sans-serif; font-weight: 600;
    font-size: 19px; color: var(--muted);
  }
</style>
</head>
<body>
  <main class="banner">
    <div class="balloons-right" role="img" aria-label="Cluster of red, teal and yellow party balloons"></div>
    <div class="photo" role="img" aria-label="Smiling family of four giving thumbs up on a sofa"></div>
    <div class="balloons-left" role="img" aria-label="Red, yellow and teal party balloons"></div>

    <svg class="wave" viewBox="0 0 1160 580" aria-hidden="true">
      <path d="M0 532 C 70 420, 150 378, 220 380 C 360 385, 520 520, 710 572 C 860 600, 1010 540, 1160 505 L1160 580 L0 580 Z" fill="var(--cyan)"/>
      <path d="M700 556 C 850 560, 1000 520, 1160 470 L1160 510 C 1010 545, 860 585, 720 566 Z" fill="var(--slate)"/>
      <path d="M0 580 C 60 460, 140 408, 220 408 C 380 410, 520 540, 720 558 C 870 570, 980 545, 1060 510 C 960 560, 860 575, 760 575 L 0 580 Z" fill="var(--banner)"/>
    </svg>

    <div class="headline-box"><h1 class="headline">GRAND OPENING</h1></div>

    <div class="brand">
      <span class="brand-mark"></span>
      <span class="brand-name">BRIGHTWAY DENTAL</span>
    </div>

    <p class="cta">Call or Text Us Now:</p>

    <div class="phone">
      <div class="phone-icon">
        <svg width="34" height="34" viewBox="0 0 24 24" aria-hidden="true">
          <path d="M6.6 10.8a15.1 15.1 0 0 0 6.6 6.6l2.2-2.2c.3-.3.7-.4 1-.2 1.1.4 2.3.6 3.6.6.6 0 1 .4 1 1V20c0 .6-.4 1-1 1C10.6 21 3 13.4 3 4c0-.6.4-1 1-1h3.5c.6 0 1 .4 1 1 0 1.3.2 2.5.6 3.6.1.3 0 .7-.2 1L6.6 10.8z" fill="var(--white)"/>
          <path d="M14 3a7 7 0 0 1 7 7M14 6.5A3.5 3.5 0 0 1 17.5 10" stroke="var(--white)" stroke-width="1.6" fill="none" stroke-linecap="round"/>
        </svg>
      </div>
      <div class="phone-number">555.014.2290</div>
    </div>

    <p class="hours">Convenient Evening &amp; Saturday Hours</p>
  </main>
</body>
</html>
```